Business Cards for new orthopaedic surgery practice

My husband and I are starting our own orthopaedic surgery practice. We are looking for a business card that is uniform, but one will have my name/title and the other will have his. You can just create one design with my name on it for now. But when I choose your design as the winning design I will ask that you add another copy with his name/title.

We are looking for classy, simple, elite all in one. We like dark blues/a little gold/yellow. Something that goes with our logo. We want our logo incorporated. Here is all the info you need:
Business name: RV Bone & Vitality Center
Location: 38517 North Willowmere Ave
Maple Hollow, FL 33490
Phone: 954-218-4063
Fax: 954-582-7341
Email: info@myrvbonecare.example

Names: Lydia Vance, M.D.
Board Certified Hand and Upper Extremity Surgeon

Ebo Dansu, M.D.
Board Certified Hip & Knee Replacement/General Orthopaedic Surgeon

Can decide what you want to put on the back. Maybe a slogan:
Strength in Motion. Care for Life

I am just going to upload our logo. The only thing is if we select you as the winning design, the location, and phone numbers may change. We will need your help to update that once fully solidified.

Industry/Entity Type

Medical

Contact Information for Business Card

Colors
0054AA
0677BA
7BADD7
CADEEF
E8F1F8
0094D4
00A9DD
6FCCEA
C7EBF8
E9F6FB

Requirements
Must have
• class, appeal,
Should not have
• We want to air on the side of masculine if we are looking at masculine vs. feminine feel. But we still want it classy, sophisticated, and something we will love

```html
<!DOCTYPE html>
<html lang="en">
<head>
<meta charset="utf-8">
<title>RV Bone &amp; Vitality Center – Business Card</title>
<link rel="stylesheet" href="https://fonts.googleapis.com/css2?family=Cinzel:wght@600&family=Arimo:wght@400&display=swap">
<style>
  :root {
    --page-bg: #e9e9e9;
    --navy-top: #2c3d67;
    --navy: #1f2c55;
    --navy-deep: #1b284f;
    --gold: #c9a45c;
    --white: #ffffff;
    --ink: #1f2c55;
  }
  * { box-sizing: border-box; margin: 0; padding: 0; }
  html, body { width: 1200px; height: 1200px; overflow: hidden; }
  body {
    background: var(--page-bg);
    font-family: "Arimo", Arial, sans-serif;
    position: relative;
  }
  .card {
    position: absolute;
    width: 688px;
    height: 393px;
    overflow: hidden;
  }
  .card--front {
    left: 267px;
    top: 159px;
    background: linear-gradient(180deg, var(--navy-top) 0%, var(--navy) 55%, var(--navy-deep) 100%);
    color: var(--white);
  }
  .card--back {
    left: 262px;
    top: 653px;
    background: var(--white);
    border-right: 2px solid var(--navy);
    border-bottom: 2px solid var(--navy);
  }
  .front-brand {
    position: absolute;
    left: 36px;
    top: 40px;
    display: flex;
    align-items: center;
    gap: 10px;
    width: 190px;
    font-family: "Cinzel", "Times New Roman", serif;
    font-weight: 600;
    font-size: 16px;
    line-height: 1.25;
    color: var(--white);
  }
  .brand-dot {
    flex: none;
    width: 14px;
    height: 14px;
    border-radius: 50%;
    background: var(--gold);
  }
  .doctor-name {
    position: absolute;
    left: 35px;
    top: 155px;
    font-family: "Cinzel", "Times New Roman", serif;
    font-weight: 600;
    font-size: 25px;
    line-height: 30px;
    color: var(--gold);
    letter-spacing: 0.3px;
  }
  .doctor-title, .address {
    position: absolute;
    left: 35px;
    font-size: 16.3px;
    line-height: 19.5px;
    color: var(--white);
  }
  .doctor-title { top: 184px; }
  .address { top: 233px; font-size: 16.5px; line-height: 21px; }
  .contact-list {
    position: absolute;
    left: 35px;
    top: 286px;
    list-style: none;
  }
  .contact-list li {
    display: flex;
    align-items: center;
    height: 20.5px;
    font-size: 16.5px;
    color: var(--white);
  }
  .contact-list svg {
    width: 14px;
    height: 14px;
    margin-right: 12px;
    fill: var(--gold);
  }
  .front-wordmark {
    position: absolute;
    right: 24px;
    bottom: 34px;
    width: 340px;
    text-align: right;
    font-family: "Cinzel", "Times New Roman", serif;
    font-weight: 600;
    font-size: 52px;
    line-height: 1.05;
    color: var(--white);
  }
  .back-brand {
    position: absolute;
    left: 0;
    right: 0;
    top: 100px;
    display: flex;
    flex-direction: column;
    align-items: center;
    gap: 20px;
    font-family: "Cinzel", "Times New Roman", serif;
    font-weight: 600;
    font-size: 38px;
    line-height: 1.15;
    color: var(--ink);
    text-align: center;
  }
  .back-brand .brand-dot { width: 18px; height: 18px; }
  .slogan {
    position: absolute;
    left: 0;
    right: 0;
    top: 335px;
    text-align: center;
    font-size: 16px;
    letter-spacing: 3.4px;
    color: var(--ink);
  }
</style>
</head>
<body>
  <section class="card card--front" aria-label="Business card front">
    <div class="front-brand"><span class="brand-dot"></span><span>RV Bone &amp; Vitality Center</span></div>

    <h1 class="doctor-name">LYDIA VANCE, M.D.</h1>
    <p class="doctor-title">Board Certified Hand and<br>Upper Extremity Surgeon</p>
    <p class="address">38517 North Willowmere Ave<br>Maple Hollow, FL 33490</p>

    <ul class="contact-list">
      <li>
        <svg viewBox="0 0 24 24" aria-hidden="true"><path d="M6.6 10.8a15.2 15.2 0 0 0 6.6 6.6l2.2-2.2c.3-.3.7-.4 1-.2 1.1.4 2.3.6 3.6.6.6 0 1 .4 1 1V20c0 .6-.4 1-1 1A17 17 0 0 1 3 4c0-.6.4-1 1-1h3.5c.6 0 1 .4 1 1 0 1.3.2 2.5.6 3.6.1.3 0 .7-.2 1z"/></svg>
        954-218-4063
      </li>
      <li>
        <svg viewBox="0 0 24 24" aria-hidden="true"><path d="M6 2h10v6H6zM3 9h18v9h-3v-3H6v3H3zM7 16h10v6H7z"/></svg>
        954-582-7341
      </li>
      <li>
        <svg viewBox="0 0 24 24" aria-hidden="true"><path d="M2 5h20v14H2zM3.5 6.5 12 13l8.5-6.5v2L12 15 3.5 8.5z" fill-rule="evenodd"/></svg>
        info@myrvbonecare.example
      </li>
      <li>
        <svg viewBox="0 0 24 24" aria-hidden="true"><path d="M12 2a10 10 0 1 0 0 20 10 10 0 0 0 0-20zm-1 17.9A8 8 0 0 1 4.1 10L9 15v1a2 2 0 0 0 2 2zm6.9-2.5A2 2 0 0 0 16 16h-1v-3a1 1 0 0 0-1-1H8v-2h2a1 1 0 0 0 1-1V7h2a2 2 0 0 0 2-2v-.4a8 8 0 0 1 2.9 12.8z"/></svg>
        www.myrvbonecare.example
      </li>
    </ul>

    <div class="front-wordmark">RV Bone &amp; Vitality Center</div>
  </section>

  <section class="card card--back" aria-label="Business card back">
    <div class="back-brand"><span class="brand-dot"></span><span>RV Bone &amp;<br>Vitality Center</span></div>
    <p class="slogan">STRENGTH IN MOTION. CARE FOR LIFE</p>
  </section>
</body>
</html>
```